I need a business card to launch my business. I am a carpenter who works with wood and metal framing. I do commercial and residential properties. I do the final fixtures in expensive residential properties. For example custom made wardrobes, prefinished doors and skirtings. I have an eye for detail and take pride in my work.

I don't want to be pigeon holed as a guy with a tool belt and a hammer. I want to look like a professional company. I want my logo to be modern and young and edgy. I don't have any preference for colours but don't want yellow.

Industry/Entity Type

Residential

Contact Information for Business Card

Oakridge Joinery Co
specialising in residential and commercial fit outs

Mark Delaney
Phone: 0417 358 260
oakridgejoineryco@mailbox-example.net

Logo styles of interest
Pictorial/Combination Logo
Wordmark Logo
Lettermark Logo

```html
<!DOCTYPE html>
<html lang="en">
<head>
<meta charset="utf-8">
<title>Oakridge Joinery Co — Business Card</title>
<link rel="stylesheet" href="https://fonts.googleapis.com/css2?family=Roboto+Slab:wght@400;700&display=swap">
<style>
  :root {
    --backdrop: #1e1e1e;
    --card: #0a0a0a;
    --gold: #d9a832;
    --white: #f2f2f2;
    --slab: "Roboto Slab", serif;
  }
  * { margin: 0; padding: 0; box-sizing: border-box; }
  html, body {
    width: 1200px;
    height: 900px;
    overflow: hidden;
    background: var(--backdrop);
  }
  .stage {
    position: relative;
    width: 1200px;
    height: 900px;
    display: flex;
    align-items: center;
    justify-content: center;
    gap: 50px;
  }
  .card {
    position: relative;
    width: 500px;
    height: 290px;
    background: var(--card);
    border-radius: 26px;
    font-family: var(--slab);
    box-shadow: 0 12px 30px rgba(0,0,0,0.45);
  }
  .brand-name {
    font-family: var(--slab);
    font-weight: 700;
    color: var(--gold);
    letter-spacing: 0.5px;
    white-space: nowrap;
  }
  /* Front */
  .card-front {
    display: flex;
    flex-direction: column;
    align-items: center;
    justify-content: center;
  }
  .card-front .brand-name {
    font-size: 34px;
    margin-bottom: 38px;
  }
  .tagline {
    text-align: center;
    font-size: 15px;
    line-height: 1.45;
    color: var(--white);
  }
  .tagline .accent { color: var(--gold); }
  /* Back */
  .card-back .brand-name {
    position: absolute;
    right: 30px;
    bottom: 110px;
    font-size: 22px;
  }
  .contact-name {
    position: absolute;
    right: 30px;
    bottom: 72px;
    font-size: 19px;
    color: var(--gold);
    text-transform: uppercase;
  }
  .contact-line {
    position: absolute;
    right: 30px;
    bottom: 48px;
    font-size: 12.5px;
    color: var(--gold);
    white-space: nowrap;
  }
  .contact-line .domain { color: var(--white); }
</style>
</head>
<body>
  <main class="stage">
    <section class="card card-front">
      <div class="brand-name">Oakridge Joinery Co</div>
      <p class="tagline">
        specialising in<br>
        <span class="accent">residential</span> and <span class="accent">commercial</span> fit outs
      </p>
    </section>

    <section class="card card-back">
      <div class="brand-name">Oakridge Joinery Co</div>
      <div class="contact-name">Mark Delaney</div>
      <div class="contact-line">P: <span class="domain">0417 358 260</span> // oakridgejoineryco<span class="domain">@mailbox-example.net</span></div>
    </section>
  </main>
</body>
</html>
```